Business Cards for IT Consulting Company (Managed Service Provider)

I am looking to have some business cards printed and would like some designs. We are an IT Consulting company based in Vancouver BC. I would like a nice clean and modern look to the cards. I have uploaded all the versions of my logo so parts can be used as needed. Here is a snippit from our website homepage:

Quillbrook Networks Ltd. is an IT Solutions Partner located in Vancouver BC, Canada. We offer IT solutions and support to customers in the greater Vancouver Area. With expertise in Microsoft platforms, as well as Linux and Mac OSX and over 12 years experience in the IT industry, Quillbrook Networks is dedicated to offering our clients top quality service and products. We take pride in the solutions we offer our customers. The greatest compliment a client can give us is to recommend our services.

Quillbrook Networks Ltd. offers a wide range of IT services from onsite service to remote support and managed service solutions. This allows clients to choose the support path that best suits their company’s needs. Supporting many different sized companies from small to enterprise level over the past 12 years Quillbrook Networks has the experience and expertise needed to ensure things run smoothly. Allowing our clients to focus on doing business.

Revolutionizing the way IT services are delivered.

Quillbrook Networks is dedicated to providing our clients with IT solutions that work and grow with them for years to come. This philosophy helps save money in the long run instead of replacing equipment constantly. Far too often IT solutions are not well thought out and while possibly solving the problem at hand, require replacement due to growth or quality within a very short time frame. Quillbrook Networks takes pride in providing solutions that will last and be able to accommodate growth without the need for replacement.

Industry/Entity Type

Information Technology

Contact Information for Business Card

Quillbrook Networks Ltd.
(Employee Name)
Eml: (Employees Email Address)
Web: quillbrook.me
Ph: 604-555-0148

Font styles to use
Serif
Sans Serif

Requirements
Must have
• The Company logo and company colors.
Nice to have
• - Our tag line: "Revolutionizing IT Services" or "Revolutionizing the way IT services are delivered."
• - Also I really like the idea of nature and technology together blending which is sort of where my logo came from so integrating that somehow onto the business cards would be great.

```html
<!DOCTYPE html>
<html lang="en">
<head>
<meta charset="utf-8">
<title>Quillbrook Networks Ltd. — Business Card</title>
<link href="https://fonts.googleapis.com/css2?family=Montserrat:wght@500;600&family=Roboto:ital,wght@0,400;0,500;1,400&display=swap" rel="stylesheet">
<style>
  :root {
    --backdrop: #bdbbbc;
    --card: #1f2022;
    --blue: #1f8fd6;
    --text-light: #d9d9d9;
    --text-muted: #b9b9b9;
    --rule: #4a4b4d;
    --strip-grey: #5b5b5d;
  }
  * { margin: 0; padding: 0; box-sizing: border-box; }
  html, body { width: 1200px; height: 1200px; overflow: hidden; }
  body { background: var(--backdrop); position: relative; font-family: "Roboto", sans-serif; }

  .card {
    position: absolute;
    width: 713px;
    height: 419px;
    background: var(--card);
    overflow: hidden;
    box-shadow: 0 14px 28px rgba(0,0,0,0.28);
  }
  .card--front { left: 238px; top: 118px; }
  .card--back  { left: 231px; top: 643px; }

  .wordmark { position: absolute; color: var(--blue); font-family: "Montserrat", sans-serif; font-weight: 600; line-height: 1; }
  .wordmark__name { display: block; font-size: 66px; letter-spacing: -0.5px; }
  .wordmark__suffix { display: block; font-size: 24px; letter-spacing: 1px; margin-top: 6px; }

  .card--front .wordmark { left: 0; right: 0; top: 152px; text-align: center; }

  .tagline-bar { position: absolute; left: 100px; right: 100px; top: 376px; display: flex; align-items: center; gap: 16px; }
  .tagline-bar__rule { flex: 1; height: 3px; }
  .tagline-bar__rule--left { background: linear-gradient(to right, rgba(31,143,214,0), var(--blue)); }
  .tagline-bar__rule--right { background: linear-gradient(to left, rgba(31,143,214,0), var(--blue)); }
  .tagline-bar__text { font-family: "Montserrat", sans-serif; font-weight: 500; font-size: 18px; color: var(--text-light); white-space: nowrap; }

  .card--back .wordmark { left: 38px; top: 70px; }

  .holder { position: absolute; right: 36px; top: 197px; text-align: right; }
  .holder__name { font-family: "Roboto", sans-serif; font-weight: 500; font-size: 25px; color: var(--blue); letter-spacing: 0.3px; }
  .holder__title { font-style: italic; font-size: 16px; color: var(--text-muted); margin-top: 6px; }

  .divider { position: absolute; left: 37px; top: 246px; width: 482px; height: 1px; background: var(--rule); }

  .contact-list { position: absolute; left: 36px; top: 277px; list-style: none; }
  .contact-list__item { display: flex; align-items: center; height: 27px; font-size: 18px; color: var(--text-light); }
  .contact-list__icon { width: 18px; height: 18px; margin-right: 18px; fill: var(--blue); }

  .slogan { position: absolute; right: 36px; top: 300px; text-align: right; font-size: 18px; line-height: 25px; color: var(--text-light); }

  .footer-bands { position: absolute; left: 0; bottom: 0; }
</style>
</head>
<body>

  <section class="card card--front" aria-label="Card front">
    <div class="wordmark">
      <span class="wordmark__name">quillbrook</span>
      <span class="wordmark__suffix">NETWORKS LTD.</span>
    </div>
    <div class="tagline-bar">
      <span class="tagline-bar__rule tagline-bar__rule--left"></span>
      <span class="tagline-bar__text">Revolutionizing IT Services</span>
      <span class="tagline-bar__rule tagline-bar__rule--right"></span>
    </div>
  </section>

  <section class="card card--back" aria-label="Card back">
    <div class="wordmark">
      <span class="wordmark__name">quillbrook</span>
      <span class="wordmark__suffix">NETWORKS LTD.</span>
    </div>

    <div class="holder">
      <div class="holder__name">Daniel Reyes</div>
      <div class="holder__title">Managing Director</div>
    </div>

    <div class="divider"></div>

    <ul class="contact-list">
      <li class="contact-list__item">
        <svg class="contact-list__icon" viewBox="0 0 24 24" aria-hidden="true"><path d="M3 8c0-2 4-4 9-4s9 2 9 4v2h-5V8c-1-.6-2.4-1-4-1s-3 .4-4 1v2H3zM6 12h12l2 8H4z"/></svg>
        604-555-0148
      </li>
      <li class="contact-list__item">
        <svg class="contact-list__icon" viewBox="0 0 24 24" aria-hidden="true"><path d="M12 2a10 10 0 1 0 0 20 10 10 0 0 0 0-20zm-1 2.1V8H7.6A8 8 0 0 1 11 4.1zm2 0A8 8 0 0 1 16.4 8H13zM5.1 10H11v4H5.1a8 8 0 0 1 0-4zM13 10h5.9a8 8 0 0 1 0 4H13zm-5.4 6H11v3.9A8 8 0 0 1 7.6 16zm5.4 0h3.4a8 8 0 0 1-3.4 3.9z"/></svg>
        www.quillbrook.me
      </li>
      <li class="contact-list__item">
        <svg class="contact-list__icon" viewBox="0 0 24 24" aria-hidden="true"><path d="M2 5h20v14H2zm2 2v.4l8 5.6 8-5.6V7zm0 2.8V17h16V9.8l-8 5.6z"/></svg>
        support@quillbrook.me
      </li>
    </ul>

    <p class="slogan">Revolutionizing the way<br>IT services are delivered</p>

    <svg class="footer-bands" width="713" height="50" viewBox="0 0 713 50" aria-hidden="true">
      <rect x="0" y="28" width="340" height="22" fill="var(--strip-grey)"/>
      <polygon points="360,0 713,0 713,50 325,50" fill="var(--blue)"/>
    </svg>
  </section>

</body>
</html>
```